Medical Billing Company Needs a Business Card Design

We need a business card design for a Florida based medical billing company called 'Clinicians Keystone Solutions'. We specialize in providing revenue cycle management services to physician and therapist offices (we're basically their back-office processing partner for providing billing software, claims submissions, A/R follow-up and patient statements & collections. Our logo is red and blue-ish, so make sure that whatever other elements are used will match appropriately. Our current business card design has a too small font size. I'd like to project an image that shows we are modern & reliable. On a side note, I'm planning on using ZUB for printing these cards.

Target Market(s)

Office managers, physicians, therapists

Industry/Entity Type

Printing

Requirements
Must have
• Logo
Name of Employee
Phone
Fax
E-mail
Website

```html
<!DOCTYPE html>
<html lang="en">
<head>
<meta charset="utf-8">
<title>Clinicians Keystone Solutions – Business Card</title>
<link rel="stylesheet" href="https://fonts.googleapis.com/css2?family=Open+Sans:wght@400;600;700&display=swap">
<style>
  :root {
    --bg: #e9eaee;
    --card-white: #ffffff;
    --navy: #2b2670;
    --violet: #4a3f93;
    --brand-red: #a8262b;
    --red-light: #c0454a;
    --text-grey: #3a3a3a;
    --white: #ffffff;
  }
  * { margin: 0; padding: 0; box-sizing: border-box; }
  html, body { width: 1200px; height: 987px; overflow: hidden; }
  body {
    background: var(--bg);
    font-family: "Open Sans", Arial, sans-serif;
    position: relative;
  }
  .card {
    position: absolute;
    width: 546px;
    height: 312px;
    border-radius: 22px;
    overflow: hidden;
    box-shadow: 0 6px 18px rgba(0,0,0,0.14);
  }
  .card-front { left: 42px; top: 338px; background: var(--card-white); }
  .card-back {
    left: 612px; top: 338px;
    background: radial-gradient(ellipse at 50% 45%, var(--red-light) 0%, var(--brand-red) 75%);
    color: var(--white);
    text-align: center;
  }
  .front-wave { position: absolute; left: 0; top: 0; width: 546px; height: 312px; }
  .brand-name {
    position: absolute;
    left: 36px; top: 24px;
    font-size: 27px;
    font-weight: 600;
    letter-spacing: 1px;
    color: var(--navy);
    display: flex; align-items: center; gap: 10px;
    line-height: 1.1;
  }
  .brand-name .brand-square {
    width: 14px; height: 14px; background: var(--brand-red); flex: none;
  }
  .contact-list {
    position: absolute; left: 36px; top: 68px;
    list-style: none;
    font-size: 12.5px;
    color: var(--text-grey);
    line-height: 19px;
  }
  .contact-list li { display: flex; align-items: center; gap: 7px; }
  .contact-list svg { width: 11px; height: 11px; flex: none; }
  .address {
    position: absolute; left: 36px; top: 148px;
    font-size: 12.5px; line-height: 17px; color: var(--text-grey);
  }
  .employee {
    position: absolute; right: 28px; bottom: 12px;
    text-align: right; color: var(--white);
    line-height: 1.25;
  }
  .employee-name { font-size: 22px; font-weight: 700; }
  .employee-name .credential { font-size: 16px; font-weight: 400; }
  .employee-title { font-size: 16px; }
  .tagline {
    margin-top: 36px;
    font-size: 13px; font-weight: 600; letter-spacing: 1.6px;
  }
  .back-name {
    margin-top: 84px;
    font-size: 26px; font-weight: 600; letter-spacing: 1px;
  }
  .back-url {
    margin-top: 88px;
    font-size: 14px; letter-spacing: 3px;
  }
</style>
</head>
<body>
  <section class="card card-front" aria-label="Business card front">
    <svg class="front-wave" viewBox="0 0 546 312" aria-hidden="true">
      <defs>
        <linearGradient id="violetBand" x1="0" y1="0" x2="1" y2="1">
          <stop offset="0" stop-color="#3a3283"/>
          <stop offset="1" stop-color="#5a4c9e"/>
        </linearGradient>
      </defs>
      <path d="M0 190 C 90 194, 150 240, 260 236 S 460 192, 546 196 L546 312 L0 312 Z" fill="#a8262b"/>
      <path d="M0 196 C 90 201, 150 247, 260 243 S 460 199, 546 203 L546 312 L0 312 Z" fill="#ffffff"/>
      <path d="M0 201 C 90 206, 150 252, 260 248 S 460 204, 546 208 L546 312 L0 312 Z" fill="url(#violetBand)"/>
    </svg>

    <div class="brand-name"><span class="brand-square"></span>CLINICIANS KEYSTONE</div>

    <ul class="contact-list">
      <li><svg viewBox="0 0 12 12"><circle cx="6" cy="6" r="6" fill="#2b2670"/><path d="M4 3l1.2 1.4-.6.8a4 4 0 0 0 2.2 2.2l.8-.6L9 8 8 9c-2.5 0-5-2.5-5-5z" fill="#fff"/></svg>123-456-0789</li>
      <li><svg viewBox="0 0 12 12"><rect x="2" y="0" width="8" height="12" rx="1.5" fill="#2b2670"/><rect x="3.5" y="2" width="5" height="6" fill="#fff"/></svg>123-456-0789</li>
      <li><svg viewBox="0 0 12 12"><rect x="0" y="2" width="12" height="8" rx="1" fill="#2b2670"/><path d="M0.5 2.5 6 7l5.5-4.5" stroke="#fff" fill="none"/></svg>info@clinicianskeystone.com</li>
      <li><svg viewBox="0 0 12 12"><circle cx="6" cy="6" r="5.5" fill="#2b2670"/><path d="M0.5 6h11M6 .5c-3 3-3 8 0 11M6 .5c3 3 3 8 0 11" stroke="#fff" stroke-width=".7" fill="none"/></svg>www.clinicianskeystone.net</li>
    </ul>

    <p class="address">2870 SE Harbor Way<br>Stuart, FL 34997</p>

    <div class="employee">
      <div class="employee-name">Daniel Whitaker, <span class="credential">CHBME</span></div>
      <div class="employee-title">President</div>
    </div>
  </section>

  <section class="card card-back" aria-label="Business card back">
    <p class="tagline">MEDICAL BILLING FOR HEALTHCARE PROFESSIONALS</p>
    <p class="back-name">CLINICIANS KEYSTONE</p>
    <p class="back-url">www.clinicianskeystone.net</p>
  </section>
</body>
</html>
```